Business card design for Automotive workshop

We need a business card for a new automotive repair and tyre shop called Keelstone Prime Automotive located in New Zealand. We are a clean, modern and fresh workshop and company.

Front needs to feature logo,
my name:
Marlo Fenwicke (director)

Address:
48 Tarn Lane
Harrowby 3742

Phone: 07 594 2713
Mobile: 027 451 9362
Email: office@keelstoneautomotive.example.nz
Website: keelstoneautomotive.example.nz

Back needs to feature an area to write down appointment details, date and time.

Also feature a list of jobs and work we do such as,
Vehicle Servicing
All Mechanical Repairs
Warrant of Fitness
Tyres & Wheel Alignments
Automotive Diagnostics
Automotive Parts & Supplies

```html
<!DOCTYPE html>
<html lang="en">
<head>
<meta charset="utf-8">
<title>Keelstone Prime Automotive – Business Card</title>
<link rel="stylesheet" href="https://fonts.googleapis.com/css2?family=Montserrat:wght@500;700&family=Oswald:wght@600&family=Didact+Gothic&display=swap">
<style>
  :root {
    --red: #e3141f;
    --ink: #1b1c1e;
    --black: #111112;
    --white: #ffffff;
    --grey-band: #e2e2e2;
    --grey-text: #4a4a4a;
    --stage: #6e7682;
  }
  * { margin: 0; padding: 0; box-sizing: border-box; }
  html, body { width: 1200px; height: 900px; overflow: hidden; }
  body {
    background: var(--stage);
    position: relative;
    font-family: "Montserrat", sans-serif;
  }
  .card {
    position: absolute;
    left: 280px;
    width: 640px;
    height: 390px;
    overflow: hidden;
  }
  .card-back { top: 40px; background: var(--ink); }
  .card-front { top: 470px; background: var(--white); }

  /* Back */
  .brand-back {
    position: absolute; top: 42px; left: 0; right: 0;
    display: flex; justify-content: center; align-items: center; gap: 12px;
  }
  .brand-mark { width: 22px; height: 22px; background: var(--red); }
  .brand-back .brand-name {
    font-family: "Montserrat", sans-serif; font-weight: 700;
    font-size: 28px; color: var(--white); letter-spacing: 0.5px;
  }
  .service-lead {
    position: absolute; top: 104px; left: 0; right: 0; text-align: center;
    color: var(--red); font-weight: 700; font-size: 17px; letter-spacing: 0.5px;
  }
  .service-list {
    position: absolute; top: 136px; left: 0; right: 0; text-align: center;
    color: var(--white); font-weight: 500; font-size: 13px; line-height: 21px;
  }
  .service-list .dot { color: var(--red); margin: 0 6px; }
  .appointment {
    position: absolute; left: 26px; right: 26px; top: 232px; bottom: 26px;
    background: var(--white); padding: 26px 26px 0;
  }
  .appointment-row {
    display: flex; align-items: baseline; gap: 8px;
    font-weight: 500; font-size: 14px; color: var(--red); height: 46px;
  }
  .appointment-row .fill { flex: 1; border-bottom: 1.5px dotted #555; transform: translateY(-3px); }

  /* Front */
  .brand-front {
    position: absolute; top: 46px; left: 40px;
    font-family: "Montserrat", sans-serif; font-weight: 700;
    font-size: 24px; color: var(--red); letter-spacing: 0.3px;
  }
  .front-bands { position: absolute; inset: 0; }
  .person { position: absolute; left: 30px; top: 250px; color: var(--white); font-family: "Oswald", sans-serif; font-style: italic; }
  .person-name { font-size: 34px; letter-spacing: 0.5px; line-height: 1.1; }
  .person-role { font-size: 18px; letter-spacing: 0.5px; }
  .contact {
    position: absolute; right: 58px; text-align: right;
    font-family: "Didact Gothic", sans-serif; color: var(--grey-text);
    white-space: nowrap;
  }
  .contact-web { top: 234px; font-size: 13px; line-height: 20px; }
  .contact-phone { top: 292px; font-size: 15px; line-height: 21px; letter-spacing: 1px; }
  .contact-address { top: 353px; font-size: 15px; color: var(--white); }
  .icon { position: absolute; right: 22px; }
  .icon-mail { top: 247px; }
  .icon-phone { top: 299px; }
  .icon-pin { top: 352px; }
</style>
</head>
<body>

<section class="card card-back" aria-label="Business card back">
  <div class="brand-back">
    <span class="brand-mark"></span>
    <span class="brand-name">Keelstone Prime Automotive</span>
  </div>
  <p class="service-lead">VEHICLE SERVICING</p>
  <p class="service-list">
    All Mechanical Repairs<span class="dot">•</span>Warrant of Fitness<span class="dot">•</span>Tyres &amp; Wheel Alignments<br>
    Automotive Diagnostics<span class="dot">•</span>Automotive Parts &amp; Supplies
  </p>
  <div class="appointment">
    <div class="appointment-row"><span>Date:</span><span class="fill"></span><span>Time:</span><span class="fill"></span></div>
    <div class="appointment-row"><span>Date:</span><span class="fill"></span><span>Time:</span><span class="fill"></span></div>
  </div>
</section>

<section class="card card-front" aria-label="Business card front">
  <p class="brand-front">Keelstone Prime Automotive</p>

  <svg class="front-bands" width="640" height="390" viewBox="0 0 640 390" aria-hidden="true">
    <polygon points="0,225 290,225 395,390 0,390" fill="var(--red)"/>
    <polygon points="296,225 640,225 640,285 334,285" fill="var(--grey-band)"/>
    <polygon points="337,289 640,289 640,337 367,337" fill="var(--grey-band)"/>
    <polygon points="370,341 640,341 640,390 401,390" fill="var(--black)"/>
  </svg>

  <div class="person">
    <p class="person-name">MARLO FENWICKE</p>
    <p class="person-role">DIRECTOR</p>
  </div>

  <p class="contact contact-web">office@keelstoneautomotive.example.nz<br>www.keelstoneautomotive.example.nz</p>
  <p class="contact contact-phone">07 594 2713<br>027 451 9362</p>
  <p class="contact contact-address">48 Tarn Lane, Harrowby 3742</p>

  <svg class="icon icon-mail" width="24" height="16" viewBox="0 0 24 16" aria-hidden="true">
    <rect x="1" y="1" width="22" height="14" fill="none" stroke="var(--black)" stroke-width="2"/>
    <polyline points="1,1 12,9 23,1" fill="none" stroke="var(--black)" stroke-width="2"/>
  </svg>
  <svg class="icon icon-phone" width="16" height="26" viewBox="0 0 16 26" aria-hidden="true">
    <rect x="1" y="1" width="14" height="24" rx="2" fill="none" stroke="var(--black)" stroke-width="2"/>
    <line x1="3" y1="20" x2="13" y2="20" stroke="var(--black)" stroke-width="1.5"/>
    <circle cx="8" cy="22.5" r="1" fill="var(--black)"/>
  </svg>
  <svg class="icon icon-pin" width="18" height="24" viewBox="0 0 18 24" aria-hidden="true">
    <path d="M9 1 C4.6 1 1 4.5 1 8.8 C1 14.6 9 23 9 23 C9 23 17 14.6 17 8.8 C17 4.5 13.4 1 9 1 Z" fill="var(--white)"/>
    <circle cx="9" cy="8.8" r="3.2" fill="var(--black)"/>
  </svg>
</section>

</body>
</html>
```